Redesign current business card for food company

i would like to redesign my business card. our company is food company, our product range from chips, juices, milk and etc (mostly dried food stuff).
I want o keep same logo but , the rest is open to new design.
you can check at our website about our company www.orvelpantry.com

Target Market(s)

most of food company

Industry/Entity Type

Business

Contact Information for Business Card

I want to keep more to blue color...

Colors
3176b5
abd036

Requirements
Must have
• our old logo
Nice to have
• we do not mind to have nice material on bus card in order to accomplish nice design. for example: using spot uv, embossed and etc.

```html
<!DOCTYPE html>
<html lang="en">
<head>
<meta charset="utf-8">
<title>Orvel Business Card</title>
<link rel="stylesheet" href="https://fonts.googleapis.com/css2?family=Cabin:wght@400;600;700&display=swap">
<style>
  :root{
    --page:#ece7e1;
    --blue-deep:#2a2bb4;
    --blue-mid:#2455c4;
    --teal:#1ba3c2;
    --ink-blue:#2436a6;
    --green:#3fae3a;
    --text:#3a3a3a;
    --rule:#c9c9c9;
    --white:#ffffff;
  }
  *{margin:0;padding:0;box-sizing:border-box}
  html,body{width:1200px;height:794px;overflow:hidden}
  body{background:var(--page);font-family:"Cabin",sans-serif;position:relative}

  .card{
    position:absolute;width:540px;height:309px;
    box-shadow:0 8px 22px rgba(0,0,0,.18);
    overflow:hidden;
  }
  .card--front{
    left:40px;top:242px;
    background:linear-gradient(200deg,var(--teal) 0%,var(--blue-mid) 45%,var(--blue-deep) 100%);
    display:flex;align-items:center;justify-content:center;
  }
  .brand-name{
    font-family:"Cabin",sans-serif;font-weight:700;letter-spacing:-1px;line-height:1;
  }
  .card--front .brand-name{color:var(--white);font-size:92px;margin-top:-14px}

  .card--back{left:620px;top:242px;background:var(--white)}
  .card--back .brand-name{
    position:absolute;right:44px;top:26px;
    color:var(--ink-blue);font-size:64px;
  }
  .divider{
    position:absolute;left:34px;right:30px;top:128px;height:1px;background:var(--rule);
  }
  .person{position:absolute;left:34px;top:146px}
  .person__name{color:var(--ink-blue);font-weight:700;font-size:19px}
  .person__title{color:var(--green);font-weight:600;font-size:14px;margin-top:1px}

  .contacts{position:absolute;left:34px;top:197px;list-style:none}
  .contacts li{display:flex;align-items:center;gap:8px;color:var(--text);font-size:14px;line-height:20px}
  .contacts svg{width:13px;height:13px;fill:var(--ink-blue);flex:none}

  .address{
    position:absolute;right:30px;top:148px;text-align:right;
    color:var(--text);font-size:14px;line-height:19px;
  }
  .address__web{color:var(--ink-blue);font-weight:700}

  .band{position:absolute;left:0;right:0;bottom:0;height:16px}
  .band__green{height:3px;background:var(--green)}
  .band__blue{height:13px;background:linear-gradient(90deg,var(--blue-deep),var(--blue-mid) 60%,var(--teal))}
</style>
</head>
<body>

<section class="card card--front" aria-label="Card front">
  <span class="brand-name">orvel</span>
</section>

<section class="card card--back" aria-label="Card back">
  <span class="brand-name">orvel</span>
  <div class="divider"></div>

  <div class="person">
    <p class="person__name">Daniel Suryaputra</p>
    <p class="person__title">President</p>
  </div>

  <ul class="contacts">
    <li>
      <svg viewBox="0 0 24 24" aria-hidden="true"><path d="M6.6 10.8a15.2 15.2 0 0 0 6.6 6.6l2.2-2.2a1 1 0 0 1 1-.25 11.4 11.4 0 0 0 3.6.57 1 1 0 0 1 1 1V20a1 1 0 0 1-1 1A17 17 0 0 1 3 4a1 1 0 0 1 1-1h3.5a1 1 0 0 1 1 1c0 1.25.2 2.45.57 3.57a1 1 0 0 1-.25 1z"/></svg>
      909 555 0142
    </li>
    <li>
      <svg viewBox="0 0 24 24" aria-hidden="true"><path d="M7 1h10a2 2 0 0 1 2 2v18a2 2 0 0 1-2 2H7a2 2 0 0 1-2-2V3a2 2 0 0 1 2-2zm0 3v14h10V4zm5 15.5a1.2 1.2 0 1 0 0 2.4 1.2 1.2 0 0 0 0-2.4z"/></svg>
      626 555 0187
    </li>
    <li>
      <svg viewBox="0 0 24 24" aria-hidden="true"><path d="M6 2h9l3 3v4h1a3 3 0 0 1 3 3v7h-4v3H6v-3H2v-7a3 3 0 0 1 3-3h1zm2 2v5h8V6h-2V4zm0 12v4h8v-4z"/></svg>
      909 555 0163
    </li>
    <li>
      <svg viewBox="0 0 24 24" aria-hidden="true"><path d="M2 5h20v14H2zm2 2v.5l8 5 8-5V7zm0 2.9V17h16V9.9l-8 5z"/></svg>
      Daniel@orvelpantry.com
    </li>
  </ul>

  <address class="address" style="font-style:normal">
    1840 Linden Ave.<br>
    Ontario CA 91761<br>
    <span class="address__web">www.orvelpantry.com</span>
  </address>

  <div class="band">
    <div class="band__green"></div>
    <div class="band__blue"></div>
  </div>
</section>

</body>
</html>
```